Motel Sign - Front

(21/03/12 - I've edited the brief and removing the words "garden view" its not fitting in the designs I'm getting and just want the word motel to be the focus. I have a template/vision of what I want - see the whiteboard sketch of what I'm looking for uploaded today. Definitely open to creatively, new designs and different ideas but the whiteboard design I've done should be a guideline. Keep it fresh/green/white. use the sample photos of green as inspiration. Thanks)
We are a motel set in the mountain country of Victoria - Australia. The front of the motel needs a fresh look. We recently removed a large amount of the garden to expose a brick courtyard fence which the front of the courtyard faces out to the main road. Within the courtyard fence there is a wooden frame and paneling.
We want to have a new sign created to slot into the wooden frame. (see photo) its the white component.
Its a very large and unusual shape and I want to keep it simple but need to fill the in the best way possible.
The space is 940mm high and 4940mm width.
The message of the sign is simple the word "MOTEL". I want people to be able to drive past and glance in and see we are a motel straight away. So the main purpose of the sign is to say "MOTEL".
I am open to colour use to match the space and have impact. I thought a background colour should be 'off white'. I'm open to the colours used to match your design as long as it matches the brief. Maybe a garden green for the emblem.
IN BRIEF:
1) the word "MOTEL"
2) Border/Background that ties in the garden.
The design should be centred, clean and simple, doesn't have to fill the whole space as long as its balanced and centred.
I like cursive and garden like designs for this one - as long its the word MOTEL still has impact. (OPEN TO NEW IDEAS)
I am also open to different ideas and suggestions if you feel you have a better way to take advantage of this space.
The sign will be 7-8 metres from the road itself.
NOTE: the photos show the space and the painted white in the space where the sign will go. The garden in front of this space will be completely cleared.
Motel

```html
<!DOCTYPE html>
<html lang="en">
<head>
<meta charset="utf-8">
<title>Motel Sign – Front</title>
<link rel="stylesheet" href="https://fonts.googleapis.com/css2?family=Russo+One&display=swap">
<style>
  :root {
    --backdrop: #e9ebe6;
    --sign-white: #fbfcf8;
    --leaf-light: #b9e06a;
    --leaf-mid: #7cbf2e;
    --leaf-deep: #3f8a1c;
    --word-green: #3d6a1e;
    --word-shadow: rgba(20, 40, 10, 0.35);
  }
  html, body {
    margin: 0;
    width: 1200px;
    height: 652px;
    overflow: hidden;
    background: var(--backdrop);
  }
  .sign {
    position: absolute;
    left: 40px;
    top: 210px;
    width: 1120px;
    height: 216px;
    background: var(--sign-white);
    box-shadow: 0 2px 6px rgba(0, 0, 0, 0.15);
    overflow: hidden;
  }
  .sign__foliage {
    position: absolute;
    inset: 0;
    width: 100%;
    height: 100%;
  }
  .sign__word {
    position: absolute;
    left: 0;
    right: 0;
    top: 50%;
    transform: translateY(-50%);
    margin: 0;
    text-align: center;
    font-family: "Russo One", sans-serif;
    font-weight: 400;
    font-size: 132px;
    line-height: 1;
    letter-spacing: 6px;
    color: var(--word-green);
    text-shadow: 3px 4px 4px var(--word-shadow);
  }
</style>
</head>
<body>
  <div class="sign">
    <svg class="sign__foliage" viewBox="0 0 1120 216" preserveAspectRatio="none">
      <defs>
        <linearGradient id="foliage-top" x1="0" y1="0" x2="1" y2="0">
          <stop offset="0" stop-color="var(--leaf-light)" stop-opacity="0"/>
          <stop offset="0.35" stop-color="var(--leaf-light)"/>
          <stop offset="1" stop-color="var(--leaf-mid)"/>
        </linearGradient>
        <linearGradient id="foliage-bottom" x1="0" y1="0" x2="1" y2="0">
          <stop offset="0" stop-color="var(--leaf-deep)"/>
          <stop offset="0.55" stop-color="var(--leaf-light)"/>
          <stop offset="1" stop-color="var(--leaf-light)" stop-opacity="0"/>
        </linearGradient>
      </defs>
      <path role="img" aria-label="Band of fresh green leaves sweeping along the top right edge"
            d="M 440 0 L 1120 0 L 1120 48 C 980 66 860 40 760 54 C 660 68 560 40 440 0 Z"
            fill="url(#foliage-top)"/>
      <path role="img" aria-label="Band of fresh green leaves sweeping along the bottom left edge"
            d="M 0 216 L 0 150 C 110 138 220 168 330 156 C 420 146 520 170 620 216 Z"
            fill="url(#foliage-bottom)"/>
    </svg>
    <h1 class="sign__word">MOTEL</h1>
  </div>
</body>
</html>
```